Matching business card for my website and logo

Hi.
I need a nice business card design that matches with my website and logo.
I'm a freelance software engineer. I focus mainly on businesses. My specialty is the development and management of complex web applications and related technologies. I'm a certified Scrum Master with hands on experience, so I can guide a software project based on agile practises as well.
I hope you can deliver something nice. Looking forward to your designs.
Updates
Here some inspiration for your design process. I really like these styles:www.designcrowd.nl/design/1446967www.designcrowd.nl/design/954677www.designcrowd.com/design/1221776www.designcrowd.nl/design/2521542www.designcrowd.nl/design/4736001en.99designs.nl/stationery-design/contests/create-business-cards-letterhead-envelopes-cyber-security-start-568299/entries/150Good luck! Added Monday, February 22, 2016
Hi designers,Thanks for all your work.Please use the color scheme that my website uses.See the attached website-design.jpg in the brief description for the complete design.I don't use the blue color anymore. The logo files are not updated yet.Thanks! Added Monday, February 22, 2016
Target Market(s)
IT businesses, other general business that require a specialist in software engineering.
Industry/Entity Type
Computer Software
Contact Information for Business Card
Tim Vosberg
professional in web development & agile project management
Mobile: 0647318290
info@lindestroom.nl
www.lindestroom.nl
Requirements
Must have
- The design must match with the colors and style of my website design. See the website-design.jpg file for the color scheme.
- My certifications should be displayed:
- Norvexa Certified Professional
- Professional Teamvane Master
- My skills should be displayed:
- web development & agile project management
- technical screening
Nice to have
- QR code to my website: www.lindestroom.nl
Should not have
- - don't use the blue color in my logo (files are outdated)
- - a font thats to small for people to read

```html
<!DOCTYPE html>
<html lang="en">
<head>
<meta charset="utf-8">
<title>Lindestroom – Business Card</title>
<link rel="stylesheet" href="https://fonts.googleapis.com/css2?family=Open+Sans:wght@400;600&display=swap">
<style>
  :root {
    --stage: #000000;
    --paper: #ffffff;
    --brand-red: #cc2431;
    --ink: #1a1a1a;
    --badge-blue: #6f93ab;
    --badge-grey: #d9dcdf;
  }
  * { margin: 0; padding: 0; box-sizing: border-box; }
  html, body {
    width: 1200px; height: 900px; overflow: hidden;
    background: var(--stage);
    font-family: "Open Sans", Arial, sans-serif;
  }
  .canvas { position: relative; width: 1200px; height: 900px; }

  .card { position: absolute; top: 275px; width: 477px; height: 294px; }
  .card--front {
    left: 116px; background: var(--paper);
    border-radius: 0 52px 0 52px;
  }
  .card--back {
    left: 622px; background: var(--brand-red);
    border-radius: 52px 0 52px 0;
  }

  .wordmark {
    position: absolute; font-weight: 400; text-transform: uppercase;
    letter-spacing: 0.08em; line-height: 1; white-space: nowrap;
  }
  .tagline { position: absolute; line-height: 1; white-space: nowrap; }

  .card--front .wordmark { left: 42px; top: 43px; font-size: 31px; color: var(--brand-red); }
  .card--front .tagline { left: 42px; top: 80px; font-size: 15px; color: var(--ink); }

  .card--back .wordmark { left: 48px; top: 106px; font-size: 42px; color: var(--paper); }
  .card--back .tagline { left: 48px; top: 163px; font-size: 21px; color: var(--paper); }

  .holder { position: absolute; right: 23px; top: 130px; text-align: right; }
  .holder__name { font-size: 18px; color: var(--brand-red); line-height: 1.2; }
  .holder__role { margin-top: 6px; font-size: 12.5px; color: var(--ink); line-height: 1.42; }

  .contact { position: absolute; right: 23px; top: 221px; list-style: none; }
  .contact__item {
    display: flex; justify-content: flex-end; align-items: center;
    font-size: 13px; color: var(--ink); height: 20px;
  }
  .contact__icon { width: 13px; height: 13px; margin-left: 9px; display: block; }

  .certifications { position: absolute; left: 42px; top: 211px; display: flex; gap: 10px; }
  .cert-seal { width: 34px; height: 58px; display: block; }
  .cert-label { width: 78px; height: 56px; display: block; }
</style>
</head>
<body>
<main class="canvas">

  <section class="card card--front" aria-label="Business card front">
    <div class="wordmark">Lindestroom</div>
    <div class="tagline">Analyze. Design. Build.</div>

    <div class="holder">
      <p class="holder__name">Tim Vosberg</p>
      <p class="holder__role">professional in web development &amp;<br>agile project management</p>
    </div>

    <div class="certifications">
      <svg class="cert-seal" viewBox="0 0 34 58" role="img" aria-label="Professional Teamvane Master certification seal">
        <path d="M9 30 L9 56 L17 50 L25 56 L25 30 Z" fill="var(--badge-blue)"/>
        <circle cx="17" cy="17" r="16" fill="var(--badge-blue)"/>
        <circle cx="17" cy="17" r="11" fill="none" stroke="var(--paper)" stroke-width="1.5"/>
      </svg>
      <svg class="cert-label" viewBox="0 0 78 56" role="img" aria-label="Norvexa Certified Professional certification mark">
        <rect x="0" y="2" width="70" height="26" rx="2" fill="var(--badge-grey)"/>
        <line x1="0" y1="38" x2="78" y2="38" stroke="var(--badge-grey)" stroke-width="1"/>
        <rect x="0" y="43" width="54" height="11" rx="2" fill="var(--badge-grey)"/>
      </svg>
    </div>

    <ul class="contact">
      <li class="contact__item">0647318290
        <svg class="contact__icon" viewBox="0 0 13 13" aria-hidden="true">
          <rect width="13" height="13" rx="2" fill="var(--brand-red)"/>
          <path d="M3.6 2.8 L5.2 2.8 L5.8 4.8 L4.9 5.6 Q5.8 7.4 7.4 8.2 L8.2 7.3 L10.2 7.9 L10.2 9.5 Q9.6 10.3 8.6 10.2 Q3.4 9.2 2.9 4 Q2.9 3.2 3.6 2.8 Z" fill="var(--paper)"/>
        </svg>
      </li>
      <li class="contact__item">info@lindestroom.nl
        <svg class="contact__icon" viewBox="0 0 13 13" aria-hidden="true">
          <rect width="13" height="13" rx="2" fill="var(--brand-red)"/>
          <rect x="2.5" y="3.8" width="8" height="5.6" fill="none" stroke="var(--paper)" stroke-width="1"/>
          <path d="M2.5 3.8 L6.5 7 L10.5 3.8" fill="none" stroke="var(--paper)" stroke-width="1"/>
        </svg>
      </li>
      <li class="contact__item">www.lindestroom.nl
        <svg class="contact__icon" viewBox="0 0 13 13" aria-hidden="true">
          <rect width="13" height="13" rx="2" fill="var(--brand-red)"/>
          <rect x="2.2" y="5.6" width="5" height="3" rx="1.5" transform="rotate(-45 4.7 7.1)" fill="none" stroke="var(--paper)" stroke-width="1.1"/>
          <rect x="5.8" y="4.4" width="5" height="3" rx="1.5" transform="rotate(-45 8.3 5.9)" fill="none" stroke="var(--paper)" stroke-width="1.1"/>
        </svg>
      </li>
    </ul>
  </section>

  <section class="card card--back" aria-label="Business card back">
    <div class="wordmark">Lindestroom</div>
    <div class="tagline">Analyze. Design. Build.</div>
  </section>

</main>
</body>
</html>
```